Allied Health team of Physiotherapists & Occupational Therapists seek a business card design

We have our new logo, we now need our new business cards and stationary. Tidewell: Oedema & Family Clinic is seeking a generic card design to represent our whole team and individual cards for each therapist that incorporates our new logo to communicate our holistic approach that is calming, nuturing, supportive and welcoming.
Our Physiotherapists and Occupational Therapists assess, treat and provide education for people who are at risk of or who have lymphoedema. This is often as a result of treatment for cancer. We provide pre-operative and post-operative management and cancer rehabilitation in our Pilates studio. Our team also consists of Physiotherapists who have a strong interest in pelvic floor and continence management for both men and women.

Target Market(s)

Mainly women health conscious

Industry/Entity Type

Allied Health: Physiotherapy / Occupational Therapy

Contact Information for Business Card

Address: 14 Gallivant Ave Frankston 3199 Phone: 84316570 fax: 8431 6578 Email: info@tidewellcareservices.com.au Website: tidewellcareservices.com.au Facebook address: facebook.com/TidewellOedemaAndFamilyCareClinic. Room to write appointments. Individual cards need to have name, office email and individual email and professional details

Requirements
Must have
• Logo as per uploaded documents

```html
<!DOCTYPE html>
<html lang="en">
<head>
<meta charset="utf-8">
<title>Tidewell Business Card</title>
<link rel="stylesheet" href="https://fonts.googleapis.com/css2?family=Arimo:wght@400;700&family=Josefin+Sans:wght@300&display=swap">
<style>
  :root {
    --backdrop: #262626;
    --card: #0b0b0b;
    --ink: #f1ead0;
    --ink-soft: #e6dfc4;
  }
  * { margin: 0; padding: 0; box-sizing: border-box; }
  html, body { width: 1200px; height: 900px; overflow: hidden; }
  body {
    background: var(--backdrop);
    font-family: "Arimo", Arial, sans-serif;
    color: var(--ink);
    display: flex;
    align-items: center;
    justify-content: center;
    gap: 40px;
  }
  .card {
    width: 540px;
    height: 310px;
    background: var(--card);
    position: relative;
    box-shadow: 0 10px 30px rgba(0,0,0,.5);
  }
  .card-front { padding: 34px 0 0 34px; }
  .holder-name {
    font-family: "Josefin Sans", Arial, sans-serif;
    font-weight: 300;
    font-size: 21px;
    letter-spacing: 2px;
    margin-bottom: 6px;
  }
  .credentials { font-size: 11.5px; line-height: 1.3; color: var(--ink-soft); }
  .roles {
    font-weight: 700;
    font-size: 12.5px;
    line-height: 1.3;
    margin-top: 14px;
    color: #fff;
  }
  .contacts { list-style: none; margin-top: 18px; font-size: 12px; line-height: 1.55; color: #fff; }
  .contacts li { display: flex; align-items: center; gap: 8px; }
  .contacts svg { width: 13px; height: 13px; flex: none; }
  .brand {
    position: absolute;
    display: flex;
    flex-direction: column;
    align-items: center;
    text-align: center;
    gap: 8px;
    color: var(--ink);
    font-size: 13px;
    line-height: 1.3;
  }
  .brand-ring {
    width: 26px; height: 26px;
    border: 1.5px solid var(--ink);
    border-radius: 50%;
  }
  .brand-name { font-weight: 400; }
  .card-front .brand { right: 26px; top: 90px; width: 140px; }
  .card-back .brand { left: 50%; top: 50%; transform: translate(-50%, -50%); width: 180px; font-size: 15px; }
</style>
</head>
<body>
  <section class="card card-front">
    <h1 class="holder-name">MAREN ELLERY</h1>
    <p class="credentials">
      B. Physio (Hons), B.App.Sci.(Human Movement/Psych)<br>
      Post Grad Certif. Exercise for Women<br>
      Post Grad Certif. Continence &amp; Pelvic Floor Rehabilitation
    </p>
    <p class="roles">
      Physiotherapist<br>
      Lymphoedema &amp; Oncology Rehabilitation<br>
      Continence &amp; Pelvic Floor
    </p>
    <ul class="contacts">
      <li>
        <svg viewBox="0 0 16 16" aria-hidden="true"><path d="M4 1.5l2.5 3-1.5 1.5c.8 2 2.5 3.7 4.5 4.5L11 9l3 2.5-1.5 2.5C7 14 2 9 2 3z" fill="none" stroke="#f1ead0" stroke-width="1.4"/></svg>
        000 3333 4444
      </li>
      <li>
        <svg viewBox="0 0 16 16" aria-hidden="true"><rect x="1.5" y="3.5" width="13" height="9" fill="none" stroke="#f1ead0" stroke-width="1.3"/><path d="M1.5 3.5L8 9l6.5-5.5" fill="none" stroke="#f1ead0" stroke-width="1.3"/></svg>
        info@tidewellcareservices.com.au
      </li>
      <li>
        <svg viewBox="0 0 16 16" aria-hidden="true"><rect x="1.5" y="3.5" width="13" height="9" fill="none" stroke="#f1ead0" stroke-width="1.3"/><path d="M1.5 3.5L8 9l6.5-5.5" fill="none" stroke="#f1ead0" stroke-width="1.3"/></svg>
        name@tidewellcareservices.com.au
      </li>
      <li>
        <svg viewBox="0 0 16 16" aria-hidden="true"><circle cx="8" cy="8" r="6.3" fill="none" stroke="#f1ead0" stroke-width="1.2"/><ellipse cx="8" cy="8" rx="2.8" ry="6.3" fill="none" stroke="#f1ead0" stroke-width="1.1"/><path d="M1.7 8h12.6M2.8 4.8h10.4M2.8 11.2h10.4" stroke="#f1ead0" stroke-width="1.1"/></svg>
        www.tidewellcareservices.com.au
      </li>
    </ul>
    <div class="brand">
      <span class="brand-ring"></span>
      <span class="brand-name">Tidewell: Oedema &amp; Family Clinic</span>
    </div>
  </section>

  <section class="card card-back">
    <div class="brand">
      <span class="brand-ring"></span>
      <span class="brand-name">Tidewell: Oedema &amp; Family Clinic</span>
    </div>
  </section>
</body>
</html>
```